Brindle Recycling needs a new web design

We need a new web design for our company based in Austin, TX. We resell and recycling electronics such as laptops, computer components, Zelvotabs, Quorns, etc. Since our inception over ten years ago, we’ve become one of the premier electronics recycling and remarketing companies in Austin, Texas.

```html
<!DOCTYPE html>
<html lang="en">
<head>
<meta charset="utf-8">
<title>Brindle Recycling</title>
<link href="https://fonts.googleapis.com/css2?family=Lato:wght@400;700;900&display=swap" rel="stylesheet">
<style>
:root{
  --blue:#1b5aa6;
  --ink:#1c1c1c;
  --text:#555;
  --white:#fff;
  --footer:#1e1e1e;
}
*{box-sizing:border-box;margin:0;padding:0}
html,body{width:1200px;height:2975px;overflow:hidden}
body{font-family:'Lato',sans-serif;background:var(--white);position:relative;color:var(--ink)}
.abs{position:absolute}
.header{top:0;left:0;width:1200px;height:95px;background:var(--white)}
.brand{display:flex;align-items:center;gap:10px}
.brand-dot{width:60px;height:60px;border-radius:50%;background:var(--blue);flex:none}
.brand-name{font-weight:900;font-size:28px;color:var(--blue);line-height:1;white-space:nowrap}
.header-brand{left:100px;top:17px}
.nav{right:100px;top:34px;display:flex;gap:30px;font-weight:700;font-size:16px;color:#222;align-items:center}
.nav .active{color:var(--blue)}
.hero{top:95px;left:0;width:1200px;height:570px;background:linear-gradient(180deg,#3f57a6 0%,#6a7fbd 45%,#8a7f7a 75%,#3a3530 100%)}
.hero-title{top:195px;width:1200px;text-align:center;font-weight:900;font-size:80px;color:var(--white)}
.hero-sub{top:314px;width:1200px;text-align:center;font-size:23px;line-height:36px;color:var(--white)}
.btn-ghost{border:2px solid var(--white);border-radius:30px;color:var(--white);font-weight:700;text-transform:uppercase;display:flex;align-items:center;justify-content:center;font-size:16px}
.hero .btn-ghost{left:494px;top:325px;width:210px;height:56px}
.dots{top:592px;left:568px;display:flex;gap:6px}
.dots span{width:12px;height:12px;border-radius:50%;border:2px solid var(--white)}
.dots span.on{background:var(--white)}
.welcome-box{left:99px;top:752px;width:600px;height:404px;border:1px solid #bdbdbd}
.welcome-title{left:133px;top:780px;font-weight:900;font-size:34px;line-height:48px}
.welcome-text{left:133px;top:888px;width:476px;font-size:14.5px;line-height:29.5px;color:var(--text)}
.btn-solid{background:var(--blue);color:var(--white);border-radius:30px;font-weight:700;font-size:15px;display:flex;align-items:center;justify-content:center;text-transform:uppercase}
.welcome-btn{left:135px;top:1075px;width:131px;height:44px}
.video{left:621px;top:791px;width:480px;height:326px;background:linear-gradient(180deg,#6a9bd3 0%,#8fb5de 50%,#6f7175 62%,#3e3f42 100%)}
.play{left:832px;top:926px;width:58px;height:58px;border-radius:50%;background:#111;border:3px solid var(--white)}
.band{top:1251px;left:0;width:1200px;height:506px;background:linear-gradient(180deg,#c9ccd0 0%,#aeb3b8 55%,#4f6a2e 80%,#3c5624 100%)}
.band-title{left:688px;top:1331px;font-weight:900;font-size:34px;color:var(--white)}
.band-text{left:690px;top:1398px;width:430px;font-size:14.5px;line-height:27px;color:var(--white)}
.band-text p+p{margin-top:22px}
.band .btn-ghost{left:690px;top:367px;width:222px;height:50px}
.cert-title{top:1848px;width:1200px;text-align:center;font-weight:900;font-size:34px}
.cert{top:1935px;width:238px;height:98px;border:1px solid #c8c8c8;display:flex;align-items:center;justify-content:center}
.badge{width:110px;height:60px;border-radius:30px;background:#c9d6ea}
.arrow{top:1962px;width:44px;height:44px;border-radius:50%;border:1px solid #aaa}
.contact{top:2128px;left:0;width:1200px;height:480px;background:linear-gradient(135deg,#1c5aa5,#2466b3 50%,#1a56a0)}
.contact-title{top:2196px;width:1200px;text-align:center;font-weight:900;font-size:34px;color:var(--white)}
.field{background:var(--white);font-size:14px;color:#666;padding:0 16px;display:flex;align-items:center}
.field.msg{align-items:flex-start;padding-top:12px}
.submit{left:535px;top:2489px;width:130px;height:45px}
.footer{top:2608px;left:0;width:1200px;height:367px;background:var(--footer)}
.footer-brand{left:98px;top:2712px;gap:8px}
.footer-brand .brand-dot{background:var(--white);width:50px;height:50px}
.footer-brand .brand-name{color:var(--white);font-size:24px}
.social{top:2806px;left:140px;display:flex;gap:8px}
.social span{width:34px;height:34px;border-radius:50%;border:1px solid var(--white)}
.f-head{top:2668px;font-size:17px;font-weight:700;color:var(--white);text-transform:uppercase}
.f-links{left:393px;top:2708px;font-size:13px;line-height:31px;color:var(--white);list-style:none}
.f-text{font-size:13px;line-height:22px;color:var(--white)}
.f-input{left:583px;top:2766px;width:254px;height:36px;background:var(--white);font-size:12px;color:#777;padding:0 12px;display:flex;align-items:center}
.f-sub{left:583px;top:2816px;width:110px;height:38px;font-size:12px}
.c-row{left:912px;display:flex;gap:18px;align-items:flex-start}
.c-row svg{flex:none;margin-top:4px}
.rule{left:99px;top:2883px;width:1002px;height:1px;background:#444}
.copy{top:2914px;width:1200px;text-align:center;font-size:12px;color:var(--white)}
</style>
</head>
<body>

<header class="abs header">
  <div class="abs brand header-brand"><span class="brand-dot"></span><span class="brand-name">Brindle Recycling</span></div>
  <nav class="abs nav">
    <span class="active">HOME</span><span>ABOUT US</span><span>SERVICES</span><span>BLOG</span><span>CONTACT US</span>
    <svg width="16" height="16" viewBox="0 0 16 16"><circle cx="6.5" cy="6.5" r="5" fill="none" stroke="#222" stroke-width="2"/><line x1="10" y1="10" x2="15" y2="15" stroke="#222" stroke-width="2.5"/></svg>
  </nav>
</header>

<section class="abs hero" role="img" aria-label="Austin city skyline at dusk">
  <div class="abs btn-ghost">Schedule a Pickup</div>
</section>
<h1 class="abs hero-title">BRINDLE RECYCLING</h1>
<p class="abs hero-sub">At Brindle Recycling, we’re committed to providing environmentally friendly<br>recycling solutions to Austin and the surrounding areas.</p>
<div class="abs dots"><span class="on"></span><span></span><span></span><span></span></div>

<div class="abs welcome-box"></div>
<h2 class="abs welcome-title">WELCOME TO<br>BRINDLE RECYCLING</h2>
<p class="abs welcome-text">What most people do not realize is electronic waste represents 2% of America’s trash in landfills, but it equals 70% of overall toxic waste. Used computer equipment is a rapidly growing source of waste across the country. Only 12.5% of electronic waste is currently recycled in the US. Computers contain valuable parts that we can recycle, and heavy metals that we should try to keep out of landfills.</p>
<div class="abs btn-solid welcome-btn">Read More</div>
<div class="abs video" role="img" aria-label="Video still of a large pile of scrap electronics under a blue sky"></div>
<div class="abs play"><svg width="52" height="52" viewBox="0 0 52 52"><polygon points="20,15 37,26 20,37" fill="#fff"/></svg></div>

<section class="abs band" role="img" aria-label="Blue recycling bin full of old computers standing on grass">
  <div class="abs btn-ghost">Schedule a Pickup</div>
</section>
<h2 class="abs band-title">ELECTRONIC RECYCLING</h2>
<div class="abs band-text">
  <p>At Brindle Recycling, we strive to keep the environment clean through our wide range of services.</p>
  <p>Our E-Waste Recycling services were designed to simplify the recycling process for residents in the Austin area. Contact us today and see how you can contribute to making this world a cleaner place.</p>
</div>

<h2 class="abs cert-title">CERTIFICATION</h2>
<div class="abs arrow" style="left:28px"><svg width="42" height="42" viewBox="0 0 42 42"><polyline points="24,14 17,21 24,28" fill="none" stroke="#777" stroke-width="2"/></svg></div>
<div class="abs cert" style="left:99px"><span class="badge"></span></div>
<div class="abs cert" style="left:353px"><span class="badge" style="background:#cfe8cf"></span></div>
<div class="abs cert" style="left:607px"><span class="badge"></span></div>
<div class="abs cert" style="left:863px"><span class="badge" style="width:70px;height:70px;border-radius:50%;background:#cfd6cf"></span></div>
<div class="abs arrow" style="left:1126px"><svg width="42" height="42" viewBox="0 0 42 42"><polyline points="18,14 25,21 18,28" fill="none" stroke="#777" stroke-width="2"/></svg></div>

<section class="abs contact"></section>
<h2 class="abs contact-title">GET IN TOUCH</h2>
<div class="abs field" style="left:260px;top:2276px;width:333px;height:40px">First Name</div>
<div class="abs field" style="left:607px;top:2276px;width:333px;height:40px">Last Name</div>
<div class="abs field" style="left:260px;top:2330px;width:333px;height:40px">Email Address</div>
<div class="abs field" style="left:607px;top:2330px;width:333px;height:40px">Phone Number</div>
<div class="abs field msg" style="left:260px;top:2384px;width:680px;height:81px">Message</div>
<div class="abs btn-ghost submit">Submit</div>

<footer class="abs footer"></footer>
<div class="abs brand footer-brand"><span class="brand-dot"></span><span class="brand-name">Brindle Recycling</span></div>
<div class="abs social"><span></span><span></span><span></span><span></span></div>

<h3 class="abs f-head" style="left:393px">Quick Links</h3>
<ul class="abs f-links"><li>Home</li><li>About us</li><li>Services</li><li>Blog</li><li>Contact Us</li></ul>

<h3 class="abs f-head" style="left:583px">Newsletter Subscription</h3>
<p class="abs f-text" style="left:583px;top:2714px;width:270px">Register your Email Address to get information about us</p>
<div class="abs f-input">Email Address</div>
<div class="abs btn-solid f-sub">Subscribe</div>

<h3 class="abs f-head" style="left:912px">Contact Us</h3>
<div class="abs c-row" style="top:2710px">
  <svg width="12" height="16" viewBox="0 0 12 16"><path d="M6 0a6 6 0 0 1 6 6c0 4-6 10-6 10S0 10 0 6a6 6 0 0 1 6-6z" fill="#fff"/><circle cx="6" cy="6" r="2.2" fill="#1e1e1e"/></svg>
  <p class="f-text" style="width:170px">4120 Larkspur Bend Austin TX USA 78700</p>
</div>
<div class="abs c-row" style="top:2773px">
  <svg width="14" height="14" viewBox="0 0 14 14"><path d="M3 0l3 3-2 2c1 2 3 4 5 5l2-2 3 3-2 3C6 14 0 8 0 3z" fill="#fff"/></svg>
  <p class="f-text">(512)555-0147</p>
</div>
<div class="abs c-row" style="top:2814px">
  <svg width="15" height="12" viewBox="0 0 15 12"><rect width="15" height="12" fill="#fff"/><polyline points="0,0 7.5,6 15,0" fill="none" stroke="#1e1e1e" stroke-width="1.5"/></svg>
  <p class="f-text">hello@brindlerecycling.com</p>
</div>

<div class="abs rule"></div>
<p class="abs copy">Copyrights © 2018, Brindle Recycling. All rights reserved.</p>

</body>
</html>
```